Rebrand stationary with recently completed logo design

Need new business cards, thank you cards, letterhead, envelopes and presentation folders. The designs will be sent to a separate production firm so I need the files to be print ready.

My contact info
Reko Haliburn

Office 604-318-5047
Fax 604-371-8054

Email reko@glazemark.ca
website www.glazemark.ca

315-14720 62nd Avenue,
Ashcombe, NS, V2K 3R8

Target Market(s)

Homeowners, businesses and contractors

Industry/Entity Type

Business

Font styles to use
Sans Serif

Colors
34a7d7

Requirements
Must have
• Like to have one side of the business card a solid color with the logo in all white. The side with all the text to be a white background
• I find the current blue on the front of the card with the white logo too dark.
Should not have
• Gradient colors

```html
<!DOCTYPE html>
<html lang="en">
<head>
<meta charset="utf-8">
<title>Glazemark Stationery</title>
<link href="https://fonts.googleapis.com/css2?family=Open+Sans:wght@400;600&display=swap" rel="stylesheet">
<style>
  :root {
    --bg: #efefef;
    --paper: #f7f7f7;
    --brand-blue: #1f92cd;
    --ink: #4a4f55;
    --ink-soft: #7a7f85;
    --rule: #8d9196;
    --white: #ffffff;
  }
  * { margin: 0; padding: 0; box-sizing: border-box; }
  html, body { width: 1200px; height: 889px; overflow: hidden; }
  body {
    background: var(--bg);
    font-family: "Open Sans", Arial, sans-serif;
    color: var(--ink);
    position: relative;
  }
  address { font-style: normal; }
  .piece { position: absolute; background: var(--paper); box-shadow: 0 1px 3px rgba(0,0,0,.12); }
  .wordmark { font-weight: 400; letter-spacing: .02em; white-space: nowrap; }

  /* Letterhead */
  .letterhead { left: 217px; top: 77px; width: 352px; height: 496px; }
  .letterhead .wordmark { position: absolute; left: 24px; top: 60px; font-size: 12px; color: var(--brand-blue); }
  .letterhead .footer-rule { position: absolute; left: 24px; right: 24px; top: 450px; border-top: 1px solid var(--rule); }
  .contact-list { position: absolute; left: 24px; top: 457px; list-style: none; font-size: 6px; line-height: 10px; color: var(--ink-soft); }
  .contact-list li { display: flex; align-items: center; gap: 4px; }
  .contact-list svg { width: 6px; height: 6px; fill: var(--brand-blue); }
  .address-block { position: absolute; right: 24px; top: 457px; text-align: right; font-size: 6px; line-height: 10px; color: var(--ink); }
  .address-block .web { font-weight: 600; }

  /* Presentation folder */
  .folder { left: 629px; top: 54px; width: 414px; height: 523px; background: var(--brand-blue); }
  .folder .spine { position: absolute; left: 0; top: 0; bottom: 0; width: 14px; border-right: 1px solid rgba(255,255,255,.18); }
  .folder .wordmark { position: absolute; left: 0; right: 0; top: 244px; text-align: center; font-size: 34px; color: var(--white); }

  /* Business cards */
  .card-back { left: 92px; top: 620px; width: 157px; height: 87px; }
  .card-back .wordmark { position: absolute; right: 10px; top: 25px; font-size: 10px; color: var(--brand-blue); }
  .card-back .name { position: absolute; left: 8px; top: 54px; font-size: 4.5px; font-weight: 600; color: var(--brand-blue); text-transform: uppercase; }
  .card-back .card-rule { position: absolute; left: 8px; right: 8px; top: 62px; border-top: .6px solid var(--rule); }
  .card-back .card-contacts { position: absolute; left: 8px; top: 64px; font-size: 3.6px; line-height: 5.4px; color: var(--ink-soft); list-style: none; }
  .card-back .card-address { position: absolute; right: 8px; top: 64px; text-align: right; font-size: 3.6px; line-height: 5.4px; color: var(--ink); }
  .card-front { left: 92px; top: 733px; width: 157px; height: 89px; background: var(--brand-blue); }
  .card-front .wordmark { position: absolute; left: 0; right: 0; top: 36px; text-align: center; font-size: 13px; color: var(--white); }

  /* Envelopes */
  .envelope-front { left: 291px; top: 629px; width: 392px; height: 189px; }
  .envelope-front .wordmark { position: absolute; left: 22px; top: 46px; font-size: 11px; color: var(--brand-blue); }
  .envelope-front .return-address { position: absolute; left: 22px; top: 64px; font-size: 5.5px; line-height: 8px; color: var(--ink); }
  .envelope-back { left: 722px; top: 629px; width: 392px; height: 188px; }
  .envelope-back .flap { position: absolute; left: 0; top: 0; width: 392px; height: 70px; }
  .envelope-back .wordmark { position: absolute; left: 0; right: 0; top: 25px; text-align: center; font-size: 11px; color: var(--white); }
</style>
</head>
<body>

  <section class="piece letterhead" aria-label="Letterhead">
    <div class="wordmark">GLAZEMARK</div>
    <div class="footer-rule"></div>
    <ul class="contact-list">
      <li><svg viewBox="0 0 10 10"><path d="M2 1h2l1 2.5-1.2 1a6 6 0 0 0 2.7 2.7l1-1.2L10 7v2c-5 .5-9-3.5-8-8z"/></svg>604-318-5047</li>
      <li><svg viewBox="0 0 10 10"><rect x="1" y="3" width="8" height="5"/><rect x="3" y="1" width="4" height="2"/></svg>604-371-8054</li>
      <li><svg viewBox="0 0 10 10"><path d="M0 2h10v6H0z"/></svg>reko@glazemark.ca</li>
    </ul>
    <address class="address-block">
      315-14720 62nd Avenue<br>
      Ashcombe, NS, V2K 3R8<br>
      <span class="web">www.glazemark.ca</span>
    </address>
  </section>

  <section class="piece folder" aria-label="Presentation folder">
    <div class="spine"></div>
    <div class="wordmark">GLAZEMARK</div>
  </section>

  <section class="piece card-back" aria-label="Business card, text side">
    <div class="wordmark">GLAZEMARK</div>
    <div class="name">Reko Haliburn</div>
    <div class="card-rule"></div>
    <ul class="card-contacts">
      <li>604-318-5047</li>
      <li>604-371-8054</li>
      <li>reko@glazemark.ca</li>
    </ul>
    <address class="card-address">
      315-14720 62nd Avenue<br>
      Ashcombe, NS, V2K 3R8<br>
      www.glazemark.ca
    </address>
  </section>

  <section class="piece card-front" aria-label="Business card, colour side">
    <div class="wordmark">GLAZEMARK</div>
  </section>

  <section class="piece envelope-front" aria-label="Envelope front">
    <div class="wordmark">GLAZEMARK</div>
    <address class="return-address">
      315-14720 62nd Avenue<br>
      Ashcombe, NS, V2K 3R8
    </address>
  </section>

  <section class="piece envelope-back" aria-label="Envelope back">
    <svg class="flap" viewBox="0 0 392 70" aria-hidden="true">
      <path d="M0 0H392L384 62Q383 68 376 68H16Q9 68 8 62Z" fill="var(--brand-blue)"/>
    </svg>
    <div class="wordmark">GLAZEMARK</div>
  </section>

</body>
</html>
```